Detail Shop Business card design

i need a business card design for my new detailing company called 'Brisk's Polish Works'. i want an all black and white design . simple, direct and to the point. i want the designer to choose a fitting font to match the logothe front should have logo, address, phone and email and the back side should have a slogan and text indicating that we offer services on anything including cars, trucks, motorcycles and RVs. slogan will read "we take pride in your ride"
maybe also very small on the back side the IG icon with Brisks_Polish_Works

phone 208.417.6352
address 3847 E Larkin Ave
Spokane WA 99214
email: BrisksPolish@mailvexo.com

Target Market(s)

all ages , auto enthusiasts

Industry/Entity Type

Automotive

Contact Information for Business Card

the front should have logo, address, phone and email and the back side should have a slogan and text indicating that we offer services on anything including cars, trucks, motorcycles and RVs. slogan will read "we take pride in your ride"

phone 208.417.6352
address 3847 E Larkin Ave
Spokane WA 99214

Colors
000000
ffffff

Requirements
Must have
• bold font and very simple design with good spacing
Nice to have
• anything creative from the designer indicating we service any types of vehicles
Should not have
• any colors ,

```html
<!DOCTYPE html>
<html lang="en">
<head>
<meta charset="utf-8">
<title>Brisk's Polish Works – Business Card</title>
<link rel="stylesheet" href="https://fonts.googleapis.com/css2?family=Bitter:wght@400;600;700&display=swap">
<style>
  :root {
    --backdrop: #2b2b2b;
    --card: #141414;
    --ink: #ffffff;
    --ink-soft: #d9d9d9;
    --rule: #bdbdbd;
  }
  * { margin: 0; padding: 0; box-sizing: border-box; }
  html, body {
    width: 1200px; height: 900px; overflow: hidden;
    background: var(--backdrop);
    font-family: "Bitter", Georgia, serif;
    color: var(--ink);
  }
  .canvas { position: relative; width: 1200px; height: 900px; }
  .card {
    position: absolute; left: 250px; width: 700px; height: 400px;
    background: var(--card);
    box-shadow: 0 10px 30px rgba(0,0,0,.45);
  }
  .card--back { top: 35px; }
  .card--front { top: 465px; }

  /* back side */
  .back-mark {
    position: absolute; left: 0; right: 0; top: 90px;
    display: flex; flex-direction: column; align-items: center; gap: 14px;
  }
  .brand-seal { width: 56px; height: 56px; border: 3px solid var(--ink-soft); border-radius: 50%; }
  .brand-name {
    font-weight: 700; font-size: 34px; letter-spacing: 1px; color: var(--ink-soft);
    text-transform: uppercase;
  }
  .slogan {
    position: absolute; left: 0; right: 0; top: 272px;
    display: flex; align-items: center; justify-content: center; gap: 14px;
    font-size: 17px; letter-spacing: 1.5px; text-transform: uppercase;
  }
  .slogan::before, .slogan::after {
    content: ""; width: 60px; height: 1px; background: var(--rule);
  }
  .services {
    position: absolute; left: 0; right: 0; top: 308px; text-align: center;
    font-size: 17px; letter-spacing: 1.5px; text-transform: uppercase;
  }

  /* front side */
  .person { position: absolute; left: 48px; top: 52px; }
  .person__name { font-size: 26px; font-weight: 600; letter-spacing: 1px; text-transform: uppercase; }
  .person__role { font-size: 14px; color: var(--ink-soft); margin-top: 2px; }
  .address { position: absolute; left: 48px; top: 150px; font-size: 17px; line-height: 1.35; }
  .contact { position: absolute; left: 48px; top: 262px; list-style: none; font-size: 17px; }
  .contact li { display: flex; align-items: center; gap: 10px; line-height: 1.45; }
  .contact svg { width: 13px; height: 13px; flex: none; }
  .front-mark {
    position: absolute; left: 400px; top: 130px; width: 270px;
    display: flex; flex-direction: column; align-items: center; gap: 18px;
  }
  .front-mark .brand-seal { width: 80px; height: 80px; border-color: var(--ink); border-width: 4px; }
  .front-mark .brand-name { color: var(--ink); font-size: 30px; text-align: center; line-height: 1.15; }
</style>
</head>
<body>
<main class="canvas">

  <section class="card card--back" aria-label="Card back">
    <div class="back-mark">
      <span class="brand-seal"></span>
      <span class="brand-name">Brisk's Polish Works</span>
    </div>
    <p class="slogan">We take pride in your ride</p>
    <p class="services">Cars – Trucks – Motorcycles and RVs</p>
  </section>

  <section class="card card--front" aria-label="Card front">
    <div class="person">
      <h1 class="person__name">Darren Colvey</h1>
      <p class="person__role">Director</p>
    </div>
    <address class="address" style="font-style:normal">
      3847 E Larkin Ave<br>Spokane WA 99214
    </address>
    <ul class="contact">
      <li>
        <svg viewBox="0 0 16 16" aria-hidden="true"><path fill="#fff" d="M4 1l3 3-2 2c1 2 3 4 5 5l2-2 3 3-2 3C7 15 1 9 1 3z"/></svg>
        208.417.6352
      </li>
      <li>
        <svg viewBox="0 0 16 16" aria-hidden="true"><rect x="1" y="3" width="14" height="10" fill="none" stroke="#fff" stroke-width="1.6"/><path d="M1 3l7 6 7-6" fill="none" stroke="#fff" stroke-width="1.6"/></svg>
        BrisksPolish@mailvexo.com
      </li>
      <li>
        <svg viewBox="0 0 16 16" aria-hidden="true"><circle cx="8" cy="8" r="6.5" fill="none" stroke="#fff" stroke-width="1.4"/><ellipse cx="8" cy="8" rx="3" ry="6.5" fill="none" stroke="#fff" stroke-width="1.2"/><path d="M1.5 8h13" stroke="#fff" stroke-width="1.2"/></svg>
        www.BrisksPolishWorks.com
      </li>
    </ul>
    <div class="front-mark">
      <span class="brand-seal"></span>
      <span class="brand-name">Brisk's Polish Works</span>
    </div>
  </section>

</main>
</body>
</html>
```